Custom hot rod builder needs a website for launch of new business where he will build luxury garages

We need a website that gives a WOW first impression for "Summit Carports". This is a new business so photos are renderings but we need it to really attract a particular audience. Our initial business is custom hot rods so now we are building garages for them. These will be like luxury "homes" for cars! I will attach our new logo. Website needs to feel powerful and prestigious.

Target Market(s)

middle aged men, car enthusiasts

Industry/Entity Type

automotive, construction

Coding

Coded - Design and coding required

Number of Pages Required

2 page

Font styles to use
Serif

Colors
0054AA
0677BA
7BADD7
CADEEF
E8F1F8

Requirements
Must have
• a WOW factor. luxury. contact form.
Nice to have
• ?

```html
<!DOCTYPE html>
<html lang="en">
<head>
<meta charset="utf-8">
<title>Summit Carports</title>
<link rel="stylesheet" href="https://fonts.googleapis.com/css2?family=Syncopate:wght@700&family=Roboto:wght@400;500;700&family=Work+Sans:wght@400;500;600&display=swap">
<style>
:root{
  --blue:#2aa6df;
  --blue-deep:#1b8fcc;
  --ink:#111319;
  --dark:#0c0e13;
  --text:#6d6f75;
  --heading:#3a3c42;
  --line:#e6e8ec;
  --white:#ffffff;
  --display:'Syncopate',sans-serif;
  --body:'Work Sans',sans-serif;
  --ui:'Roboto',sans-serif;
}
*{margin:0;padding:0;box-sizing:border-box}
html,body{width:1200px;height:4003px;overflow:hidden}
body{position:relative;background:var(--white);font-family:var(--body);color:var(--text)}
.abs{position:absolute}
.shapes{position:absolute;left:0;top:0;width:1200px;height:4003px}
/* header */
.site-header{position:absolute;left:0;top:0;width:1200px;height:112px;background:var(--white);z-index:5}
.brand{position:absolute;left:110px;top:30px;display:flex;align-items:center;gap:12px}
.brand-dot{width:50px;height:50px;border-radius:50%;background:var(--blue)}
.brand-name{font-family:var(--ui);font-weight:700;font-size:22px;color:var(--blue);letter-spacing:.5px}
.main-nav{position:absolute;left:389px;top:47px;display:flex;gap:24px;font-family:var(--ui);font-weight:700;font-size:12.5px;color:#55575c}
.main-nav .active{color:var(--blue)}
.call{position:absolute;left:891px;top:35px;display:flex;gap:19px;align-items:center}
.call-icon{width:41px;height:41px;border-radius:4px;background:var(--blue);display:flex;align-items:center;justify-content:center}
.call small{display:block;font-family:var(--ui);font-weight:700;font-size:11px;color:#55575c}
.call strong{font-family:var(--ui);font-weight:700;font-size:14.5px;color:var(--blue)}
/* hero */
.hero-copy{position:absolute;left:0;top:300px;width:1200px;text-align:center;color:var(--white)}
.hero-copy h1{font-family:var(--display);font-size:37px;letter-spacing:2px;text-shadow:0 2px 8px rgba(0,0,0,.4)}
.hero-copy p{font-family:var(--ui);font-weight:700;font-size:17px;line-height:27px;margin:14px auto 0;width:560px;text-shadow:0 1px 4px rgba(0,0,0,.5)}
.btn{display:inline-block;background:var(--blue);color:var(--white);font-family:var(--ui);font-weight:700;font-size:14px;border-radius:4px;text-align:center}
.hero-btn{position:absolute;left:527px;top:432px;width:145px;height:50px;line-height:50px}
.arrow-round{position:absolute;width:36px;height:36px;border-radius:50%;background:var(--white);display:flex;align-items:center;justify-content:center}
.badge{position:absolute;left:540px;top:660px;width:120px;height:120px;border-radius:50%;background:rgba(255,255,255,.85);display:flex;align-items:center;justify-content:center}
.badge span{width:76px;height:76px;border-radius:50%;background:var(--white);box-shadow:0 2px 10px rgba(0,0,0,.15);display:flex;align-items:center;justify-content:center;font-family:var(--ui);font-weight:700;font-size:22px;color:var(--blue)}
/* section titles */
.section-title{position:absolute;left:0;width:1200px;text-align:center;font-family:var(--display);font-size:32px;color:var(--ink);letter-spacing:1px}
.section-title em{font-style:normal;color:var(--blue)}
.section-title.light{color:var(--white)}
/* about */
.about-text{position:absolute;left:125px;top:885px;width:950px;text-align:center;font-size:14.5px;line-height:26px;color:#707278}
.about-btn{position:absolute;left:532px;top:1021px;width:136px;height:50px;line-height:50px}
/* services */
.service-card{position:absolute;top:1344px;width:309px;height:356px;background:var(--white);border-radius:8px;text-align:center}
.service-card .photo{position:absolute;left:7px;top:7px;width:295px;height:195px;border-radius:6px}
.service-card h3{position:absolute;top:226px;width:100%;font-family:var(--ui);font-weight:500;font-size:17px;color:var(--blue)}
.service-card p{position:absolute;top:262px;left:20px;right:20px;font-size:14px;line-height:26px;color:var(--text)}
/* features */
.feature{position:absolute;top:2013px;width:232px;height:309px;background:var(--white);border-radius:10px;box-shadow:0 4px 22px rgba(0,0,0,.1);text-align:center}
.feature .ico{position:absolute;left:72px;top:34px;width:88px;height:88px;border-radius:50%;background:var(--blue);display:flex;align-items:center;justify-content:center}
.feature h3{position:absolute;top:142px;width:100%;font-family:var(--ui);font-weight:700;font-size:16px;line-height:26px;color:#55575c;letter-spacing:.5px}
.feature p{position:absolute;top:205px;left:14px;right:14px;font-size:13.5px;line-height:24px;color:#7c7e84}
/* testimonials */
.review{position:absolute;top:2688px;width:313px;height:194px;background:var(--white);border-radius:6px;text-align:center}
.avatar{position:absolute;left:124px;top:-34px;width:66px;height:66px;border-radius:50%;border:3px solid var(--white);background:linear-gradient(#b9c2c9,#6b7680)}
.review h4{position:absolute;top:52px;width:100%;font-family:var(--ui);font-weight:700;font-size:14px;color:var(--blue)}
.review h4 span{font-family:var(--body);font-weight:400;font-size:13px;color:#55575c}
.stars{position:absolute;top:74px;width:100%;color:#f07f1c;font-size:12px;letter-spacing:2px}
.review p{position:absolute;top:102px;left:18px;right:18px;font-size:13.5px;line-height:24px;color:#707278}
.chev{position:absolute;top:2766px}
/* contact */
.field{position:absolute;background:var(--white);border-radius:6px;box-shadow:0 2px 12px rgba(0,0,0,.09);font-size:14.5px;color:#55575c;padding:18px 18px}
.submit{position:absolute;left:524px;top:3462px;width:152px;height:50px;display:flex;align-items:center;justify-content:center;gap:12px}
/* footer */
.footer-brand{position:absolute;left:110px;top:3800px;width:150px;text-align:center}
.footer-brand .dot{width:84px;height:84px;border-radius:50%;background:var(--blue);margin:0 auto 14px}
.footer-brand strong{font-family:var(--ui);font-weight:700;font-size:19px;color:var(--blue);line-height:24px}
.vline{position:absolute;top:3710px;width:1px;height:232px;background:#2b2e36}
.fcol{position:absolute;top:3709px;color:var(--white)}
.fcol h5{font-family:var(--ui);font-weight:700;font-size:15.5px;margin-bottom:18px}
.fcol li{list-style:none;font-family:var(--ui);font-size:13.5px;height:36px;display:flex;align-items:center;gap:18px}
.fcol li i{width:12px;height:12px;border-radius:50%;background:var(--blue);position:relative}
.fcol li i:after{content:"";position:absolute;left:3px;top:4px;border-left:5px solid var(--white);border-top:2px solid transparent;border-bottom:2px solid transparent}
.crow{display:flex;align-items:center;gap:23px;font-family:var(--ui);font-size:13.5px;line-height:22px;position:absolute;left:0;white-space:nowrap}
.cring{width:46px;height:46px;border-radius:50%;border:1.5px solid #c9ccd2;display:flex;align-items:center;justify-content:center}
.footer-rule{position:absolute;left:111px;top:3948px;width:978px;height:1px;background:#2b2e36}
.copy{position:absolute;left:0;top:3968px;width:1200px;text-align:center;font-family:var(--ui);font-size:12.5px;color:var(--white)}
.social{position:absolute;top:3960px;width:30px;height:30px;border-radius:50%;background:var(--blue)}
</style>
</head>
<body>

<svg class="shapes" viewBox="0 0 1200 4003" aria-hidden="false">
  <defs>
    <linearGradient id="heroGrad" x1="0" y1="0" x2="1" y2="1">
      <stop offset="0" stop-color="#5a3a24"/>
      <stop offset=".45" stop-color="#8a5a34"/>
      <stop offset=".75" stop-color="#2f4a44"/>
      <stop offset="1" stop-color="#3b4d6a"/>
    </linearGradient>
    <linearGradient id="aboutGrad" x1="0" y1="0" x2="0" y2="1">
      <stop offset="0" stop-color="#f1f2f4"/>
      <stop offset=".5" stop-color="#e9eaec"/>
      <stop offset="1" stop-color="#f7f7f8"/>
    </linearGradient>
    <linearGradient id="darkGrad" x1="0" y1="0" x2="1" y2="0">
      <stop offset="0" stop-color="#1a1c22"/>
      <stop offset="1" stop-color="#0a0b0f"/>
    </linearGradient>
  </defs>

  <!-- about backdrop -->
  <rect x="0" y="560" width="1200" height="600" fill="url(#aboutGrad)" role="img" aria-label="Faint rendering of a modern luxury garage building"/>

  <!-- hero -->
  <path d="M0 545 C150 640 360 750 560 738 C800 720 1000 580 1200 548 V600 C1000 630 800 750 560 760 C360 768 150 690 0 610 Z" fill="var(--blue)"/>
  <path d="M0 112 H1200 V548 C1000 580 800 720 560 738 C360 750 150 640 0 545 Z" fill="url(#heroGrad)" role="img" aria-label="Rendering of a luxury car garage interior with classic hot rods and wall art"/>

  <!-- services band -->
  <path d="M0 1292 C300 1190 600 1122 820 1132 C1000 1142 1130 1230 1200 1322 V1712 C1000 1810 800 1870 560 1872 C300 1874 100 1800 0 1710 Z" fill="var(--blue)"/>
  <path d="M0 1305 C300 1205 600 1140 820 1150 C990 1160 1110 1250 1200 1345 V1690 C1000 1790 800 1852 560 1852 C300 1852 100 1780 0 1690 Z" fill="url(#darkGrad)" role="img" aria-label="Dark backdrop of a parked car in shadow"/>

  <!-- testimonials band -->
  <path d="M0 2560 C250 2455 500 2398 800 2398 C1000 2398 1120 2460 1200 2510 V2890 C1000 2975 760 3055 520 3055 C300 3055 120 2985 0 2935 Z" fill="var(--blue)" role="img" aria-label="Blue tinted backdrop of a modern garage home with palm trees"/>
  <path d="M1200 2890 C1000 2975 760 3055 520 3055 C760 3040 1000 2960 1200 2870 Z" fill="var(--blue-deep)"/>

  <!-- footer band -->
  <path d="M300 3660 C550 3580 800 3570 1000 3600 C1100 3620 1160 3660 1200 3690 V3760 C1150 3700 1080 3660 1000 3640 Z" fill="var(--blue)"/>
  <path d="M0 3740 C250 3650 500 3590 760 3590 C950 3592 1100 3660 1200 3760 V4003 H0 Z" fill="var(--dark)"/>
</svg>

<header class="site-header">
  <div class="brand"><span class="brand-dot"></span><span class="brand-name">SUMMIT CARPORTS</span></div>
  <nav class="main-nav">
    <span class="active">HOME</span><span>ABOUT US</span><span>SERVICES</span><span>RESOURCES</span><span>CONTACT US</span>
  </nav>
  <div class="call">
    <span class="call-icon"><svg width="18" height="18" viewBox="0 0 24 24"><path fill="#fff" d="M6.6 10.8a15.1 15.1 0 0 0 6.6 6.6l2.2-2.2c.3-.3.7-.4 1-.2 1.1.4 2.3.6 3.6.6.6 0 1 .4 1 1V20c0 .6-.4 1-1 1C10.6 21 3 13.4 3 4c0-.6.4-1 1-1h3.5c.6 0 1 .4 1 1 0 1.3.2 2.5.6 3.6.1.3 0 .7-.2 1z"/></svg></span>
    <div><small>CALL US:</small><strong>+1 (555) 014 2290</strong></div>
  </div>
</header>

<section class="hero-copy">
  <h1>SUMMIT CARPORTS</h1>
  <p>Lorem ipsum dolor sit amet, consectetur adipiscing elit, sed do eiusmod tempor incididunt ut laborea.</p>
</section>
<a class="btn hero-btn">GET STARTED</a>
<span class="arrow-round" style="left:42px;top:360px"><svg width="12" height="14" viewBox="0 0 12 14"><path d="M8 2 3 7l5 5" stroke="#2aa6df" stroke-width="2" fill="none"/></svg></span>
<span class="arrow-round" style="left:1122px;top:360px"><svg width="12" height="14" viewBox="0 0 12 14"><path d="M4 2l5 5-5 5" stroke="#2aa6df" stroke-width="2" fill="none"/></svg></span>
<div class="badge"><span>SC</span></div>

<h2 class="section-title" style="top:818px">ABOUT <em>SC</em></h2>
<p class="about-text">Lorem ipsum dolor sit amet, consectetur adipiscing elit, sed do eiusmod tempor incididunt ut labore et dolore magna aliqua. Ut enim ad minim veniam, quis nostrud exercitation ullamco laboris nisi ut aliquip ex ea commodo consequat. Duis aute irure dolor in reprehenderit in voluptate velit esse cillum dolore eu fugiat nulla pariatur. Excepteur sint occaecat cupidatat non proident, sunt in culpa qui officia deserunt mollit anim id est laboexercitation ullamco laboris nisi ut aliquip rum.</p>
<a class="btn about-btn">LEARN MORE</a>

<h2 class="section-title light" style="top:1255px">OUR SERVICES</h2>
<article class="service-card" style="left:111px">
  <div class="photo" role="img" aria-label="Rendering of a red sports car inside a modern garage" style="background:linear-gradient(135deg,#5f6064,#b9b5ae 55%,#7a2a22)"></div>
  <h3>LOREM IPSUM DOLOR</h3>
  <p>Lorem ipsum dolor sit amet, consec tetur adipiscing elit, sed do eiusmod tempor ut laborea.</p>
</article>
<article class="service-card" style="left:446px">
  <div class="photo" role="img" aria-label="Rendering of a black classic hot rod in front of a garage wall" style="background:linear-gradient(135deg,#8a8a88,#3a3b3d 55%,#1d1e20)"></div>
  <h3>LOREM IPSUM DOLOR</h3>
  <p>Lorem ipsum dolor sit amet, consec tetur adipiscing elit, sed do eiusmod tempor ut laborea.</p>
</article>
<article class="service-card" style="left:780px">
  <div class="photo" role="img" aria-label="Rendering of a red supercar in a parking garage" style="background:linear-gradient(135deg,#6c6e74,#a34042 55%,#4a4c52)"></div>
  <h3>LOREM IPSUM DOLOR</h3>
  <p>Lorem ipsum dolor sit amet, consec tetur adipiscing elit, sed do eiusmod tempor ut laborea.</p>
</article>

<h2 class="section-title" style="top:1933px"><em>WHY</em> CHOOSE US</h2>
<div class="feature" style="left:111px">
  <span class="ico"><svg width="44" height="44" viewBox="0 0 44 44" fill="none" stroke="#fff" stroke-width="2"><circle cx="22" cy="17" r="5"/><path d="M13 32c1-6 5-9 9-9s8 3 9 9"/><circle cx="8" cy="12" r="2"/><circle cx="36" cy="12" r="2"/><circle cx="8" cy="30" r="2"/><circle cx="36" cy="30" r="2"/></svg></span>
  <h3>OWNERSHIP<br>ADVANTAGE</h3>
  <p>Lorem ipsum dolor sit amet, con sectetur adipiscing elit, sed do eiusmodea.</p>
</div>
<div class="feature" style="left:360px">
  <span class="ico"><svg width="44" height="44" viewBox="0 0 44 44" fill="none" stroke="#fff" stroke-width="2"><path d="M6 18 22 8l16 10v18H6z"/><rect x="12" y="20" width="20" height="16"/><path d="M12 25h20M12 30h20"/></svg></span>
  <h3>UNDER<br>YOUR CONTROL</h3>
  <p>Lorem ipsum dolor sit amet, con sectetur adipiscing elit, sed do eiusmodea.</p>
</div>
<div class="feature" style="left:609px">
  <span class="ico"><svg width="44" height="44" viewBox="0 0 44 44" fill="none" stroke="#fff" stroke-width="2"><circle cx="14" cy="14" r="4"/><circle cx="30" cy="14" r="4"/><circle cx="22" cy="22" r="4"/><path d="M6 34c0-6 4-10 8-10M38 34c0-6-4-10-8-10M14 36c0-5 4-8 8-8s8 3 8 8"/></svg></span>
  <h3>COMMUNITY<br>AMENITIES</h3>
  <p>Lorem ipsum dolor sit amet, con sectetur adipiscing elit, sed do eiusmodea.</p>
</div>
<div class="feature" style="left:857px">
  <span class="ico"><svg width="44" height="44" viewBox="0 0 44 44" fill="none" stroke="#fff" stroke-width="2"><path d="M22 6 36 11v10c0 9-6 15-14 18C14 36 8 30 8 21V11z"/><path d="m15 22 5 5 9-10"/></svg></span>
  <h3>SAFE<br>&amp; SECURE</h3>
  <p>Lorem ipsum dolor sit amet, con sectetur adipiscing elit, sed do eiusmodea.</p>
</div>

<h2 class="section-title light" style="top:2557px">TESTIMONIALS</h2>
<div class="review" style="left:111px">
  <span class="avatar" role="img" aria-label="Customer portrait"></span>
  <h4>JAKE MILLER, <span>United States</span></h4>
  <div class="stars">★★★★★</div>
  <p>Sed ut perspiciatis unde omnis iste nat us error sit volup tatem accusanti um dolore mque laudantieaumea.</p>
</div>
<div class="review" style="left:444px">
  <span class="avatar" role="img" aria-label="Customer portrait"></span>
  <h4>JAKE MILLER, <span>United States</span></h4>
  <div class="stars">★★★★★</div>
  <p>Sed ut perspiciatis unde omnis iste nat us error sit volup tatem accusanti um dolore mque laudantieaumea.</p>
</div>
<div class="review" style="left:776px">
  <span class="avatar" role="img" aria-label="Customer portrait"></span>
  <h4>JAKE MILLER, <span>United States</span></h4>
  <div class="stars">★★★★★</div>
  <p>Sed ut perspiciatis unde omnis iste nat us error sit volup tatem accusanti um dolore mque laudantieaumea.</p>
</div>
<svg class="chev" style="left:50px" width="24" height="36" viewBox="0 0 24 36"><path d="M18 4 6 18l12 14" stroke="#fff" stroke-width="4" fill="none"/></svg>
<svg class="chev" style="left:1128px" width="24" height="36" viewBox="0 0 24 36"><path d="M6 4l12 14L6 32" stroke="#fff" stroke-width="4" fill="none"/></svg>

<h2 class="section-title" style="top:3123px">CONTACT <em>US</em></h2>
<form>
  <div class="field" style="left:209px;top:3197px;width:386px;height:50px">First Name</div>
  <div class="field" style="left:606px;top:3197px;width:386px;height:50px">Last Name</div>
  <div class="field" style="left:209px;top:3264px;width:386px;height:50px">Your Phone</div>
  <div class="field" style="left:606px;top:3264px;width:386px;height:50px">Your Email</div>
  <div class="field" style="left:209px;top:3330px;width:783px;height:120px">How Can we help you?</div>
  <a class="btn submit">SUBMIT <svg width="16" height="16" viewBox="0 0 16 16"><path fill="#fff" d="M15 1 1 7l5 2 1 5 2-3 4 3z"/></svg></a>
</form>

<footer>
  <div class="footer-brand"><div class="dot"></div><strong>SUMMIT<br>CARPORTS</strong></div>
  <span class="vline" style="left:327px"></span>
  <span class="vline" style="left:568px"></span>
  <span class="vline" style="left:812px"></span>
  <div class="fcol" style="left:388px">
    <h5>NAVIGATION</h5>
    <ul><li><i></i>Home</li><li><i></i>About Us</li><li><i></i>Services</li><li><i></i>Resources</li><li><i></i>Contact Us</li></ul>
  </div>
  <div class="fcol" style="left:617px">
    <h5>OTHER LINKS</h5>
    <ul><li><i></i>Site Map</li><li><i></i>Privacy Policy</li><li><i></i>Terms Of Use</li></ul>
  </div>
  <div class="fcol" style="left:851px;width:260px;height:240px">
    <h5>CONTACT US</h5>
    <div class="crow" style="top:38px"><span class="cring"><svg width="14" height="18" viewBox="0 0 14 18"><path d="M7 1a6 6 0 0 0-6 6c0 4 6 10 6 10s6-6 6-10a6 6 0 0 0-6-6z" fill="none" stroke="#fff" stroke-width="1.5"/><circle cx="7" cy="7" r="2" fill="#fff"/></svg></span><span>465, Lorum Ipsum Dolore,<br>United States</span></div>
    <div class="crow" style="top:106px"><span class="cring"><svg width="14" height="14" viewBox="0 0 24 24"><path fill="#fff" d="M6.6 10.8a15.1 15.1 0 0 0 6.6 6.6l2.2-2.2c.3-.3.7-.4 1-.2 1.1.4 2.3.6 3.6.6.6 0 1 .4 1 1V20c0 .6-.4 1-1 1C10.6 21 3 13.4 3 4c0-.6.4-1 1-1h3.5c.6 0 1 .4 1 1 0 1.3.2 2.5.6 3.6.1.3 0 .7-.2 1z"/></svg></span><span>+ 1 (555) 014 2290</span></div>
    <div class="crow" style="top:165px"><span class="cring"><svg width="16" height="12" viewBox="0 0 16 12"><rect x="1" y="1" width="14" height="10" fill="none" stroke="#fff" stroke-width="1.5"/><path d="m1 1 7 6 7-6" fill="none" stroke="#fff" stroke-width="1.5"/></svg></span><span>info@summitcarports.com</span></div>
  </div>
  <div class="footer-rule"></div>
  <p class="copy">© 2022 SUMMIT CARPORTS &nbsp;/&nbsp; All Rights Reserved</p>
  <span class="social" style="left:946px" aria-label="Social profile"></span>
  <span class="social" style="left:982px" aria-label="Social profile"></span>
  <span class="social" style="left:1020px" aria-label="Social profile"></span>
  <span class="social" style="left:1057px" aria-label="Social profile"></span>
</footer>

</body>
</html>
```